Elevating our current Business Card Design

We want to elevate our current business card with a new design to look like a zenith 300 company. We are a premium lubricant distributor (oil and grease).
We need 2 versions, version 1 is as per the uploaded a copy of our current business card with the English version.
For our Chinese version we need to use the front to be English in English and have the back of the card designed exactly like the front for all info to be in Chinese.
The design template needs to be such that we can amend the template with adding different information for each person's card.
The background colour of the card can be changed- we just need to clearly see all information on the card and logos.
The QJR and Ember steady logos cannot have any colour or display changes- only use the logos attached.
All logos need to be included and all information from the attached current card

```html
<!DOCTYPE html>
<html lang="en">
<head>
<meta charset="utf-8">
<title>Norvane Oil Distributors – Business Card</title>
<link rel="stylesheet" href="https://fonts.googleapis.com/css2?family=Open+Sans:wght@400;600;700&display=swap">
<style>
  :root {
    --stage: #232323;
    --card-dark: #1f1f22;
    --brand-red: #ec2a32;
    --deep-red: #8e141a;
    --gold: #e8ac2c;
    --badge-orange: #f07a22;
    --badge-grey: #8a8a8c;
    --ink-light: #ffffff;
    --shadow: rgba(0, 0, 0, 0.55);
  }
  * { margin: 0; padding: 0; box-sizing: border-box; }
  html, body {
    width: 1200px; height: 780px; overflow: hidden;
    background: var(--stage);
    font-family: "Open Sans", sans-serif;
  }
  .stage { position: relative; width: 1200px; height: 780px; }

  .card {
    position: absolute;
    width: 580px; height: 331px;
    border-radius: 22px;
    overflow: hidden;
    box-shadow: 0 14px 30px var(--shadow);
  }

  /* back of card */
  .card-back { left: 70px; top: 56px; background: var(--brand-red); }
  .card-back .pattern-field {
    position: absolute; inset: 0;
    background: linear-gradient(135deg, #ef3038 0%, var(--brand-red) 55%, #dc242c 100%);
  }
  .card-back .brand-name {
    position: absolute; right: 54px; top: 140px;
    color: var(--ink-light);
    font-weight: 700; font-size: 40px; letter-spacing: 1px;
  }

  /* front of card */
  .card-front { left: 550px; top: 404px; background: var(--card-dark); }
  .card-front .swoosh { position: absolute; left: 0; top: 0; }

  .holder {
    position: absolute; right: 30px; top: 22px;
    text-align: right; color: var(--ink-light);
  }
  .holder-name { font-weight: 600; font-size: 27px; line-height: 1.1; }
  .holder-role { font-size: 14px; letter-spacing: 0.3px; margin-top: 2px; }

  .address {
    position: absolute; left: 34px; top: 182px;
    color: var(--ink-light); font-size: 12.5px; line-height: 1.35;
  }
  .contacts {
    position: absolute; left: 34px; top: 226px;
    list-style: none; color: var(--ink-light); font-size: 12.5px;
  }
  .contacts li { display: flex; align-items: center; gap: 8px; height: 18px; }
  .contacts svg { width: 12px; height: 12px; flex: none; }

  .badges {
    position: absolute; right: 40px; top: 168px;
    display: flex; gap: 18px;
  }
  .badge { width: 44px; height: 44px; }

  .brand-lockup {
    position: absolute; right: 22px; bottom: 28px;
    display: flex; height: 46px;
    border: 1.5px solid var(--brand-red);
  }
  .lockup-own {
    display: flex; align-items: center; gap: 8px;
    padding: 0 14px; color: var(--brand-red);
    font-weight: 700; font-size: 18px;
  }
  .lockup-dot { width: 10px; height: 10px; border-radius: 50%; background: var(--brand-red); }
  .lockup-partner {
    display: flex; align-items: center;
    padding: 0 16px; background: var(--brand-red);
    color: var(--card-dark); font-weight: 700; font-size: 20px; letter-spacing: 0.5px;
  }
</style>
</head>
<body>
<main class="stage">

  <section class="card card-back" aria-label="Card back">
    <div class="pattern-field" role="img" aria-label="Red field with a repeating embossed brand-symbol pattern"></div>
    <div class="brand-name">Norvane</div>
  </section>

  <section class="card card-front" aria-label="Card front">
    <svg class="swoosh" width="580" height="331" viewBox="0 0 580 331" aria-hidden="true">
      <defs>
        <linearGradient id="band-red" x1="0" y1="1" x2="1" y2="0">
          <stop offset="0" stop-color="#ef2d28"/>
          <stop offset="0.45" stop-color="#e42a24"/>
          <stop offset="1" stop-color="#8e141a"/>
        </linearGradient>
      </defs>
      <path d="M0 0 H580 V48 C555 98 470 118 330 126 C200 133 80 120 0 64 Z" fill="url(#band-red)"/>
      <path d="M14 86 C90 128 210 144 335 136 C470 127 560 104 580 58" fill="none" stroke="#e8ac2c" stroke-width="5"/>
    </svg>

    <div class="holder">
      <div class="holder-name">Mara Quinlan</div>
      <div class="holder-role">Administration Executive</div>
    </div>

    <p class="address">48 Freight Parade<br>Ashbury, WA 6190</p>

    <ul class="contacts">
      <li><svg viewBox="0 0 12 12"><path d="M2 1 L4.5 1 L5.2 3.6 L3.8 4.6 C4.5 6 5.8 7.4 7.4 8.2 L8.4 6.8 L11 7.5 L11 10 C6 10.5 1.5 6 2 1Z" fill="#ec2a32"/></svg>1300 555 014</li>
      <li><svg viewBox="0 0 12 12"><rect x="3" y="0.8" width="6" height="10.4" rx="1" fill="none" stroke="#ec2a32" stroke-width="1.2"/></svg>+61 400 555 271</li>
      <li><svg viewBox="0 0 12 12"><rect x="1" y="4" width="10" height="7" rx="1" fill="#ec2a32"/><rect x="3" y="1" width="6" height="4" fill="none" stroke="#ec2a32" stroke-width="1"/></svg>+61 8 5550 3126</li>
      <li><svg viewBox="0 0 12 12"><circle cx="6" cy="6" r="5" fill="none" stroke="#ec2a32" stroke-width="1.2"/><path d="M1 6 H11 M6 1 C3.5 3.5 3.5 8.5 6 11 M6 1 C8.5 3.5 8.5 8.5 6 11" fill="none" stroke="#ec2a32" stroke-width="0.9"/></svg>www.norvaneoil.com</li>
      <li><svg viewBox="0 0 12 12"><rect x="1" y="2.5" width="10" height="7.5" rx="0.8" fill="#ec2a32"/><path d="M1.5 3 L6 6.8 L10.5 3" fill="none" stroke="#1f1f22" stroke-width="1"/></svg>mara.quinlan@norvaneoil.com</li>
    </ul>

    <div class="badges" aria-label="Certification badges">
      <svg class="badge" viewBox="0 0 44 44" role="img" aria-label="Certification badge"><circle cx="22" cy="22" r="20" fill="none" stroke="#8a8a8c" stroke-width="4"/><circle cx="22" cy="22" r="13" fill="#f07a22"/></svg>
      <svg class="badge" viewBox="0 0 44 44" role="img" aria-label="Certification badge"><circle cx="22" cy="22" r="20" fill="none" stroke="#8a8a8c" stroke-width="4"/><circle cx="22" cy="22" r="13" fill="#f07a22"/></svg>
      <svg class="badge" viewBox="0 0 44 44" role="img" aria-label="Certification badge"><circle cx="22" cy="22" r="20" fill="none" stroke="#8a8a8c" stroke-width="4"/><circle cx="22" cy="22" r="13" fill="#f07a22"/></svg>
    </div>

    <div class="brand-lockup">
      <div class="lockup-own"><span class="lockup-dot"></span>Norvane</div>
      <div class="lockup-partner">KESTREL</div>
    </div>
  </section>

</main>
</body>
</html>
```